Verlindo Magician

I want the business card for my business to give to people who watch that later I will be employed to show magic here is my website http://www.verlindoillusions.example/I want the interesting design , i am very opened for formal and informal, I watch a lot of design so don't stick to the common shape and form but i hope it can also be produced the thing to write on will be the same as in picture that i will upload , i also will upload the logo for you that so can be easy to useDenis CostilleMagicianMAGICIAN VERLINDO 17 rue des Tilleuls - 25000 BESANÇON contact@verlindoillusions.example tel. 0381 946 157 tel. 0674 219 503

```html
<!DOCTYPE html>
<html lang="fr">
<head>
<meta charset="utf-8">
<title>Verlindo Magician – Business Card</title>
<link rel="stylesheet" href="https://fonts.googleapis.com/css2?family=Josefin+Sans:wght@300&family=Open+Sans:wght@400;700;800&display=swap">
<style>
  :root {
    --backdrop: #e4e4e4;
    --card: #ffffff;
    --ink: #111111;
    --accent-red: #e0231c;
    --art-dark: #1a1a1a;
    --art-mid: #3a3a3a;
    --text-soft: #222222;
  }
  * { margin: 0; padding: 0; box-sizing: border-box; }
  html, body {
    width: 1200px; height: 900px; overflow: hidden;
    background: var(--backdrop);
  }
  .canvas {
    position: relative; width: 1200px; height: 900px;
    font-family: "Open Sans", Arial, sans-serif; color: var(--ink);
  }
  .card {
    position: absolute; left: 320px; width: 560px; height: 320px;
    background: var(--card); border-radius: 26px; overflow: hidden;
    border-bottom: 6px solid var(--accent-red);
    box-shadow: 0 10px 24px rgba(0,0,0,0.18);
  }
  .card--front { top: 90px; }
  .card--back { top: 490px; }

  /* Front */
  .front-portrait {
    position: absolute; left: 210px; top: 46px; width: 140px; height: 140px;
    border-radius: 40px 40px 20px 20px;
    background: linear-gradient(180deg, var(--art-mid), var(--art-dark));
  }
  .front-wordmark {
    position: absolute; left: 0; right: 0; top: 200px; text-align: center;
    font-family: "Josefin Sans", Arial, sans-serif; font-weight: 300;
    color: var(--ink);
  }
  .front-wordmark .name { display: block; font-size: 40px; letter-spacing: 3px; line-height: 1; }
  .front-wordmark .role { display: block; font-size: 11px; letter-spacing: 4px; margin-top: 6px; }

  /* Back */
  .back-portrait {
    position: absolute; left: 0; bottom: 0; width: 270px; height: 230px;
    border-radius: 0 120px 0 0;
    background: linear-gradient(160deg, var(--art-mid), var(--art-dark) 60%);
  }
  .contact {
    position: absolute; left: 286px; top: 40px; width: 262px;
    font-size: 13px; line-height: 1.32; color: var(--text-soft);
  }
  .contact__name { font-weight: 800; font-size: 20px; color: var(--ink); line-height: 1.1; }
  .contact__title { margin-bottom: 6px; }
  .contact__line { display: flex; align-items: center; gap: 6px; white-space: nowrap; }
  .contact__line svg { width: 12px; height: 12px; flex: none; fill: var(--ink); }
  .contact__company { font-weight: 700; color: var(--ink); margin-top: 4px; font-size: 14px; }
</style>
</head>
<body>
<main class="canvas">

  <section class="card card--front" aria-label="Card front">
    <div class="front-portrait" role="img" aria-label="Black and white illustration of the magician holding a playing card"></div>
    <div class="front-wordmark">
      <span class="name">VERLINDO</span>
      <span class="role">MAGICIEN</span>
    </div>
  </section>

  <section class="card card--back" aria-label="Card back">
    <div class="back-portrait" role="img" aria-label="Large black and white illustration of the magician holding a playing card"></div>
    <div class="contact">
      <div class="contact__name">MARC RAVOULET</div>
      <div class="contact__title">Magician</div>
      <div class="contact__line">
        <svg viewBox="0 0 24 24" aria-hidden="true"><path d="M6.6 10.8a15.1 15.1 0 0 0 6.6 6.6l2.2-2.2a1 1 0 0 1 1-.25 11.4 11.4 0 0 0 3.6.57 1 1 0 0 1 1 1V20a1 1 0 0 1-1 1A17 17 0 0 1 3 4a1 1 0 0 1 1-1h3.5a1 1 0 0 1 1 1c0 1.25.2 2.45.57 3.57a1 1 0 0 1-.25 1z"/></svg>
        0381 946 157
      </div>
      <div class="contact__line">
        <svg viewBox="0 0 24 24" aria-hidden="true"><path d="M6.6 10.8a15.1 15.1 0 0 0 6.6 6.6l2.2-2.2a1 1 0 0 1 1-.25 11.4 11.4 0 0 0 3.6.57 1 1 0 0 1 1 1V20a1 1 0 0 1-1 1A17 17 0 0 1 3 4a1 1 0 0 1 1-1h3.5a1 1 0 0 1 1 1c0 1.25.2 2.45.57 3.57a1 1 0 0 1-.25 1z"/></svg>
        0674 219 503
      </div>
      <div class="contact__line">
        <svg viewBox="0 0 24 24" aria-hidden="true"><path d="M2 5h20v14H2z M4 7v.5l8 5 8-5V7l-8 5z" fill-rule="evenodd"/></svg>
        contact@verlindoillusions.example
      </div>
      <div class="contact__line">
        <svg viewBox="0 0 24 24" aria-hidden="true"><circle cx="12" cy="12" r="10"/></svg>
        www.verlindoillusions.example
      </div>
      <div class="contact__company">MAGICIAN VERLINDO</div>
      <div>17 rue des Tilleuls - 25000</div>
      <div>BESANÇON</div>
    </div>
  </section>

</main>
</body>
</html>
```